Visitenkartenvorlage ändern
Zielgruppe
Eventmanagement
Aufgabenstellung
Die beiliegende Visitenkarte wäre das "perfekte" Logo für mich. Da es sich hierbei aber um eine Vorlage eines Online-Druck-Anbieters handelt, darf es leider nur für deren Drucke verwendet werden und nicht für Printwerbung, Homepage etc. Daher sollte es genügend verfremdet werden, so dass ich es verwenden kann.

```html
<!DOCTYPE html>
<html lang="de">
<head>
<meta charset="utf-8">
<title>Well Arranged – Visitenkarte</title>
<link rel="stylesheet" href="https://fonts.googleapis.com/css2?family=Open+Sans:wght@400;600&family=Pinyon+Script&display=swap">
<style>
  :root {
    --backdrop: #2a2b2d;
    --card: #ecebea;
    --card-back: #e9e8e7;
    --ink: #5d5d5d;
    --accent: #a8368e;
    --accent-soft: #c76fb3;
    --rule: #8d8d8d;
    --pattern: #f3f2f1;
  }
  * { box-sizing: border-box; margin: 0; padding: 0; }
  html, body {
    width: 1163px; height: 1200px; overflow: hidden;
    background: var(--backdrop);
    font-family: "Open Sans", Arial, sans-serif;
    color: var(--ink);
  }
  .canvas { position: relative; width: 1163px; height: 1200px; }
  .card {
    position: absolute; left: 249px; width: 698px; height: 401px;
    background: var(--card);
  }
  .card--front { top: 161px; }
  .card--back { top: 658px; background: var(--card-back); }

  .line { position: absolute; left: 0; width: 100%; text-align: center; white-space: nowrap; }
  .brand-name {
    font-size: 25px; font-weight: 400; letter-spacing: 5px; line-height: 30px;
  }
  .tagline {
    font-size: 19px; font-variant: small-caps; letter-spacing: 2px; line-height: 24px;
  }
  .web { font-size: 15px; letter-spacing: 0.5px; line-height: 20px; text-transform: uppercase; }

  .ornament-area {
    position: absolute;
    background: radial-gradient(ellipse at center, var(--accent-soft) 0%, var(--accent) 60%, rgba(168,54,142,0) 72%);
  }
  .card--front .ornament-area { left: 243px; top: 150px; width: 233px; height: 110px; }
  .card--back .ornament-area { left: 277px; top: 20px; width: 144px; height: 78px; }

  .pattern-field {
    position: absolute; left: 0; top: 100px; width: 100%; height: 301px;
    background: linear-gradient(180deg, var(--pattern) 0%, var(--card-back) 100%);
  }
  .border-band { position: absolute; top: 82px; }
  .border-band--left { left: 11px; width: 288px; }
  .border-band--right { left: 400px; width: 290px; }

  .holder {
    font-family: "Pinyon Script", cursive;
    color: var(--accent-soft); font-size: 34px; line-height: 40px;
  }
  .contact { position: absolute; top: 338px; font-size: 16px; letter-spacing: 2px; line-height: 22px; }
  .contact--mail { left: 59px; font-variant: small-caps; font-size: 18px; }
  .contact--phone { right: 55px; letter-spacing: 1.5px; font-size: 17px; }
</style>
</head>
<body>
<main class="canvas">
  <section class="card card--front" aria-label="Visitenkarte Vorderseite">
    <p class="line brand-name" style="top:74px">WELL ARRANGED</p>
    <div class="ornament-area" role="img" aria-label="Verschnörkeltes florales Ornament in Magenta"></div>
    <p class="line tagline" style="top:292px">Events und mehr</p>
    <p class="line web" style="top:327px">www.well-arranged.de</p>
  </section>

  <section class="card card--back" aria-label="Visitenkarte Rückseite">
    <div class="pattern-field" role="img" aria-label="Zartes helles Rankenmuster im Hintergrund"></div>
    <div class="ornament-area" role="img" aria-label="Verschnörkeltes florales Ornament in Magenta"></div>
    <svg class="border-band border-band--left" height="14" viewBox="0 0 288 14" aria-hidden="true">
      <line x1="0" y1="7" x2="288" y2="7" stroke="var(--rule)" stroke-width="1.5"/>
      <rect x="54" y="3" width="14" height="8" fill="var(--accent)"/>
      <rect x="138" y="3" width="14" height="8" fill="var(--accent)"/>
      <rect x="222" y="3" width="14" height="8" fill="var(--accent)"/>
    </svg>
    <svg class="border-band border-band--right" height="14" viewBox="0 0 290 14" aria-hidden="true">
      <line x1="0" y1="7" x2="290" y2="7" stroke="var(--rule)" stroke-width="1.5"/>
      <rect x="58" y="3" width="14" height="8" fill="var(--accent)"/>
      <rect x="140" y="3" width="14" height="8" fill="var(--accent)"/>
      <rect x="222" y="3" width="14" height="8" fill="var(--accent)"/>
    </svg>
    <p class="line brand-name" style="top:138px">WELL ARRANGED</p>
    <p class="line tagline" style="top:186px">Events und mehr</p>
    <p class="line holder" style="top:240px">Brunela Torvik</p>
    <p class="contact contact--mail">info@well-arranged.de</p>
    <p class="contact contact--phone">+ 49 170&nbsp; 5550142</p>
  </section>
</main>
</body>
</html>
```